Dalvick's Business Card

I need some designs for a new business card including the new logo attached. An old example of our business card is also attached to show all the data that should be included on the new design.
**I added some more examples someone had mocked up**

Contact Information for Business Card

Should include all info on other examples uploaded.

```html
<!DOCTYPE html>
<html lang="en">
<head>
<meta charset="utf-8">
<title>Dalvick's Business Card</title>
<link rel="stylesheet" href="https://fonts.googleapis.com/css2?family=Montserrat:wght@500;700;800&family=Oswald:wght@600&display=swap">
<style>
  :root {
    --brand-blue: #0a72c0;
    --brand-red: #ec1c24;
    --paper: #ffffff;
    --backdrop: #2b2b2b;
  }
  * { box-sizing: border-box; margin: 0; padding: 0; }
  html, body { width: 1200px; height: 1015px; overflow: hidden; background: var(--backdrop); }
  body { font-family: "Montserrat", sans-serif; position: relative; }

  .card {
    position: absolute;
    left: 250px;
    width: 700px;
    height: 400px;
    overflow: hidden;
    box-shadow: 0 10px 30px rgba(0,0,0,.5);
  }
  .card--front { top: 70px; background: var(--brand-blue); }
  .card--back { top: 545px; background: var(--paper); }

  /* Front */
  .front__top-band {
    position: absolute; left: 0; top: 0; width: 100%; height: 58px;
    background: var(--brand-red); color: var(--paper);
    display: flex; align-items: center; justify-content: center;
    font-weight: 800; font-size: 23px; letter-spacing: .5px;
    white-space: nowrap;
  }
  .front__bottom-band {
    position: absolute; left: 0; bottom: 0; width: 100%; height: 80px;
    padding: 0 24px;
    background: var(--brand-red); color: var(--paper);
    display: flex; align-items: center; justify-content: center;
    font-family: "Oswald", sans-serif; font-weight: 600; font-size: 21px;
    text-transform: uppercase; letter-spacing: .2px; white-space: nowrap;
  }
  .brand {
    position: absolute; display: flex; align-items: center; gap: 16px;
  }
  .brand__dot { width: 62px; height: 62px; border-radius: 50%; flex: none; }
  .brand__name { font-weight: 700; font-size: 64px; line-height: 1; letter-spacing: 1px; text-transform: uppercase; white-space: nowrap; }
  .brand__service { font-weight: 500; font-size: 12.5px; letter-spacing: 1.4px; text-transform: uppercase; margin-top: 4px; white-space: nowrap; }

  .card--front .brand { left: 150px; top: 150px; color: var(--paper); }
  .card--front .brand__dot { background: var(--paper); }

  /* Back */
  .back__blue-band {
    position: absolute; left: 0; top: 200px; width: 100%; height: 110px;
    background: var(--brand-blue);
  }
  .back__red-band {
    position: absolute; left: 0; top: 310px; width: 100%; height: 90px;
    background: var(--brand-red);
    display: flex; align-items: center; color: var(--paper);
    font-weight: 700; font-size: 19px; letter-spacing: 1px; text-transform: uppercase;
    white-space: nowrap;
  }
  .card--back .brand { left: 120px; top: 80px; color: var(--brand-blue); }
  .card--back .brand__dot { background: var(--brand-red); }
  .card--back .brand__service { color: var(--brand-red); }

  .owner {
    position: absolute; left: 0; top: 200px; width: 370px; height: 110px;
    display: flex; align-items: center; justify-content: center;
    color: var(--paper); font-weight: 700; font-size: 28px; letter-spacing: 1.5px; text-transform: uppercase;
    white-space: nowrap;
  }
  .divider { position: absolute; width: 1px; background: rgba(255,255,255,.45); }
  .divider--contact { left: 370px; top: 215px; height: 80px; }
  .divider--badges { left: 350px; top: 325px; height: 60px; }

  .contact { position: absolute; left: 395px; top: 218px; color: var(--paper); font-size: 18px; font-weight: 500; white-space: nowrap; }
  .contact__row { display: flex; align-items: center; gap: 12px; height: 38px; }
  .contact__icon { width: 20px; height: 20px; flex: none; }

  .badge { width: 350px; text-align: center; }
</style>
</head>
<body>

<section class="card card--front" aria-label="Card front">
  <div class="front__top-band">Serves Ridgeford, IA &amp; Surrounding Areas</div>
  <div class="brand">
    <span class="brand__dot"></span>
    <div>
      <div class="brand__name">Dalvick's</div>
      <div class="brand__service">Air Conditioning &amp; Heating Service</div>
    </div>
  </div>
  <div class="front__bottom-band">Call today for all your HVAC, refrigeration &amp; plumbing needs</div>
</section>

<section class="card card--back" aria-label="Card back">
  <div class="brand">
    <span class="brand__dot"></span>
    <div>
      <div class="brand__name">Dalvick's</div>
      <div class="brand__service">Air Conditioning &amp; Heating Service</div>
    </div>
  </div>

  <div class="back__blue-band"></div>
  <div class="owner">Glen Dalvick</div>
  <div class="divider divider--contact"></div>
  <div class="contact">
    <div class="contact__row">
      <svg class="contact__icon" viewBox="0 0 24 24" aria-hidden="true"><path fill="#fff" d="M6.6 10.8a15.1 15.1 0 0 0 6.6 6.6l2.2-2.2a1 1 0 0 1 1-.25 11.4 11.4 0 0 0 3.6.57 1 1 0 0 1 1 1V20a1 1 0 0 1-1 1A17 17 0 0 1 3 4a1 1 0 0 1 1-1h3.5a1 1 0 0 1 1 1c0 1.25.2 2.45.57 3.57a1 1 0 0 1-.25 1z"/></svg>
      <span>555.014.2290</span>
    </div>
    <div class="contact__row">
      <svg class="contact__icon" viewBox="0 0 24 24" aria-hidden="true"><rect x="2" y="5" width="20" height="14" fill="none" stroke="#fff" stroke-width="2"/><path d="M2 5l10 8 10-8" fill="none" stroke="#fff" stroke-width="2"/></svg>
      <span>hvacdalvick@mailbox.com</span>
    </div>
  </div>

  <div class="back__red-band">
    <span class="badge">Licensed &amp; Insured</span>
    <span class="badge">Family Owned &amp; Operated</span>
  </div>
  <div class="divider divider--badges"></div>
</section>

</body>
</html>
```